Brell Stone Company Business Cards

Front and Back Business Card - logo and text setup - cool design. I need workable photoshop or illustrator files so I can setup each employee card with design that is created
Updates

Hi everyone, thank you for the great entries. Please no more white and blue cards - there are so many already - black and silver only now please. thanks!

Target Market(s)

Construction Industry - Facility Managers

Industry/Entity Type

Construction

Contact Information for Business Card

I really like contemporary simplistic looks - clean neat....not opposed to seeing some black backrounds

Requirements
Must have
• Logo/website address with design on front only - www.brellstone-example.com (logo attached)
• Back:
• Name/Title/Company Address/Phone/email address
Nice to have
• Cool design
Should not have
• Nothing gimmicky like Fire or Water - since we are a Fire Protection company - it has all been done

```html
<!DOCTYPE html>
<html lang="en">
<head>
<meta charset="utf-8">
<title>Brell Stone Company Business Cards</title>
<link rel="stylesheet" href="https://fonts.googleapis.com/css2?family=Poppins:wght@400;500;600;700&display=swap">
<style>
  :root {
    --stage: #e9e9ea;
    --black: #1a1b1d;
    --black-deep: #0f1011;
    --silver: #b9bdc3;
    --silver-dark: #868b92;
    --paper: #f6f7f8;
    --ink: #2e2f31;
    --white: #ffffff;
  }
  * { box-sizing: border-box; margin: 0; padding: 0; }
  html, body {
    width: 1200px; height: 920px; overflow: hidden;
    background: var(--stage);
    font-family: "Poppins", sans-serif;
  }
  .stage { position: relative; width: 1200px; height: 920px; }

  .card {
    position: absolute; top: 314px;
    width: 536px; height: 298px;
    box-shadow: 0 6px 16px rgba(0,0,0,0.2);
    overflow: hidden;
  }

  /* Front */
  .card-front { left: 46px; background: var(--black); }
  .front-name {
    position: absolute; left: 0; right: 0; top: 112px;
    text-align: center;
    font-weight: 700; font-size: 50px; letter-spacing: -1px; line-height: 60px;
    color: var(--black-deep);
  }
  .front-web {
    position: absolute; left: 0; right: 0; top: 258px;
    text-align: center;
    font-size: 14px; letter-spacing: 1px; color: var(--white);
  }
  .front-web .accent { color: var(--silver); }

  /* Back */
  .card-back { left: 629px; background: var(--paper); }
  .back-name {
    position: absolute; left: 36px; top: 124px;
    font-weight: 700; font-size: 34px; letter-spacing: -1px; line-height: 42px;
    color: var(--black);
  }
  .divider {
    position: absolute; left: 262px; top: 70px;
    width: 2px; height: 156px; background: var(--silver);
  }
  .contact {
    position: absolute; left: 284px; top: 66px; width: 220px;
    color: var(--ink); font-size: 12px; line-height: 20px;
  }
  .contact .person {
    font-size: 16px; font-weight: 600; color: var(--black);
    letter-spacing: 0.3px; line-height: 24px;
  }
  .contact .role { margin-bottom: 2px; color: var(--silver-dark); }
  .contact .line { display: flex; align-items: center; gap: 9px; }
  .contact .line svg { width: 11px; height: 11px; flex: none; }
  .contact .address { margin-bottom: 2px; }

  .stripe { position: absolute; bottom: 0; height: 6px; }
  .stripe-black { left: 0; width: 263px; background: var(--black); }
  .stripe-silver { left: 263px; right: 0; background: var(--silver); }
</style>
</head>
<body>
<main class="stage">

  <section class="card card-front" aria-label="Card front">
    <div class="front-name">Brell Stone</div>
    <div class="front-web">www.<span class="accent">brellstone-example</span>.com</div>
  </section>

  <section class="card card-back" aria-label="Card back">
    <div class="back-name">Brell Stone</div>
    <div class="divider"></div>
    <div class="contact">
      <div class="person">DANA WHITFIELD</div>
      <div class="role">Senior Consultant</div>
      <div class="address">48 Harbor Point Road<br>Easton, NY 11820</div>
      <div class="line">
        <svg viewBox="0 0 12 12" aria-hidden="true"><path fill="#868b92" d="M2.5 1h2l1 2.6-1.3 1A6.5 6.5 0 0 0 7.4 7.8l1-1.3L11 7.5v2A1.5 1.5 0 0 1 9.5 11 8.5 8.5 0 0 1 1 2.5 1.5 1.5 0 0 1 2.5 1z"/></svg>
        <span>(555) 014-2291</span>
      </div>
      <div class="line">
        <svg viewBox="0 0 12 12" aria-hidden="true"><g fill="#868b92"><rect x="3" y="1" width="6" height="3"/><rect x="1" y="4.5" width="10" height="4.5" rx="1"/><rect x="3" y="8" width="6" height="3" fill="#f6f7f8" stroke="#868b92" stroke-width="1"/></g></svg>
        <span>(555) 014-2292</span>
      </div>
      <div class="line">
        <svg viewBox="0 0 12 12" aria-hidden="true"><rect x="1" y="2.5" width="10" height="7" fill="none" stroke="#868b92" stroke-width="1.2"/><path d="M1 3l5 3.5L11 3" fill="none" stroke="#868b92" stroke-width="1.2"/></svg>
        <span>info@brellstone-example.com</span>
      </div>
      <div class="line">
        <svg viewBox="0 0 12 12" aria-hidden="true"><g fill="none" stroke="#868b92" stroke-width="1.1"><circle cx="6" cy="6" r="4.8"/><ellipse cx="6" cy="6" rx="2" ry="4.8"/><path d="M1.2 6h9.6"/></g></svg>
        <span>www.brellstone-example.com</span>
      </div>
    </div>
    <div class="stripe stripe-black"></div>
    <div class="stripe stripe-silver"></div>
  </section>

</main>
</body>
</html>
```